Internal web page of multinational company - Portfolio of reports

We need to improve the look & feel of an existing internal HTML page.
We use it as a portfolios where users go and see a list of existing reports as "tiles". The HTML page is automatically generated by a javascript that reads the contents to display from an HTML file.
What is needs is a "face lift" in the design of the page.
Currently we use icons on the top right of each tile to denote the type of technology used on the report and also colons for the same purpose. The attached screenshots will be self explanatory.
Across the top we have "tabs" that, once selected change the tiles.
Need a proposal for new design that keeps is as clean as possible, specially the home page that should be very light (Plimbo like).
The idea for this page is to serve as a "one stop shop" and become a bookmark for everyone in the company.
Looking for a wow effect that make is visually

Target Market(s)

Internal employees

Industry/Entity Type

It Company

Coding

Coded - Design and coding required

Number of Pages Required

2 page

Requirements
Must have
• Should not change the logo or its position from the bottom left.
• Page must be as clean as possible and
Nice to have
• Welcome to change the logo on the top left. This page is from the CSU M&I (Mni) which stands for Central Support Unit - Metrics & Insight.
Should not have
• Do no use red, this is the color of our competitor. The blue on the bottom is standard for our logo

```html
<!DOCTYPE html>
<html lang="en">
<head>
<meta charset="utf-8">
<title>CSU M&amp;I – Finance Reports</title>
<link href="https://fonts.googleapis.com/css2?family=Oswald:wght@300;400&family=Open+Sans:wght@400;600&display=swap" rel="stylesheet">
<style>
  :root {
    --brand-blue: #5068a6;
    --nav-text: #1f3779;
    --tile-title: #3d5799;
    --tile-icon: #6b6b6b;
    --tile-border: #e4e6ea;
    --tile-bg: rgba(255,255,255,0.82);
    --header-bg: #ffffff;
    --field-border: #dcdfe4;
    --footer-text: #ffffff;
    --logo-text: #1c1c24;
  }
  * { box-sizing: border-box; margin: 0; padding: 0; }
  html, body { width: 1200px; height: 735px; overflow: hidden; }
  body {
    position: relative;
    font-family: "Open Sans", Arial, sans-serif;
    background: #f3f4f6;
  }
  .city-backdrop {
    position: absolute; left: 0; top: 103px; width: 1200px; height: 558px;
    background: linear-gradient(180deg, #f4f5f7 0%, #eef0f3 40%, #e3e7ec 75%, #d8dde4 100%);
  }
  .site-header {
    position: absolute; left: 0; top: 0; width: 1200px; height: 103px;
    background: var(--header-bg);
    box-shadow: 0 1px 3px rgba(0,0,0,0.08);
  }
  .brand {
    position: absolute; left: 24px; top: 31px; display: flex; align-items: center; gap: 8px;
  }
  .brand-mark {
    width: 38px; height: 38px; border-radius: 50%; background: var(--brand-blue);
  }
  .brand-name {
    font-family: "Oswald", Arial, sans-serif; font-weight: 400; font-size: 30px;
    color: var(--logo-text); line-height: 38px; letter-spacing: 0.3px;
  }
  .main-nav { position: absolute; left: 0; top: 0; width: 845px; height: 103px; }
  .main-nav a {
    position: absolute; top: 0; height: 103px; line-height: 101px;
    font-family: "Oswald", Arial, sans-serif; font-weight: 300; font-size: 16px;
    color: var(--nav-text); text-decoration: none; white-space: nowrap;
  }
  .main-nav a.is-active {
    left: 273px; width: 80px; text-align: center;
    background: var(--brand-blue); color: #fff;
  }
  .main-nav a:nth-child(2) { left: 370px; }
  .main-nav a:nth-child(3) { left: 452px; }
  .main-nav a:nth-child(4) { left: 498px; }
  .main-nav a:nth-child(5) { left: 635px; }
  .main-nav a:nth-child(6) { left: 688px; }
  .main-nav a:nth-child(7) { left: 769px; }
  .search {
    position: absolute; left: 850px; top: 32px; display: flex; height: 35px;
  }
  .search-field {
    width: 226px; height: 35px; border: 1px solid var(--field-border); border-radius: 3px;
    padding-left: 12px; font-size: 13px; line-height: 33px; color: #555;
    background: #fff;
  }
  .search-buttons {
    margin-left: 9px; display: flex; border: 1px solid var(--field-border); border-radius: 3px;
  }
  .search-buttons span {
    width: 46px; height: 33px; display: flex; align-items: center; justify-content: center;
    color: #444; font-weight: 600; font-size: 15px;
  }
  .search-buttons span + span { width: 41px; border-left: 1px solid var(--field-border); }
  .report-grid {
    position: absolute; left: 24px; top: 151px;
    display: grid; grid-template-columns: repeat(4, 271px);
    column-gap: 20.5px; row-gap: 22px;
  }
  .report-tile {
    position: relative; width: 271px; height: 98px;
    background: var(--tile-bg); border: 1px solid var(--tile-border);
  }
  .report-title {
    position: absolute; left: 15px; top: 23px; display: flex; align-items: center; gap: 8px;
    font-size: 14px; color: var(--tile-title); white-space: nowrap;
  }
  .report-title svg { width: 13px; height: 13px; flex: none; }
  .report-tools {
    position: absolute; right: 16px; top: 69px; display: flex; gap: 7px;
  }
  .report-tools svg { width: 14px; height: 14px; fill: var(--tile-icon); }
  .site-footer {
    position: absolute; left: 0; top: 661px; width: 1200px; height: 74px;
    background: var(--brand-blue); color: var(--footer-text);
  }
  .copyright { position: absolute; left: 97px; top: 26px; font-size: 12px; }
  .social { position: absolute; left: 556px; top: 27px; display: flex; gap: 5px; }
  .social .share-tile { width: 19px; height: 19px; border-radius: 4px; background: #fff; }
  .social svg { width: 19px; height: 19px; }
  .help {
    position: absolute; left: 928px; top: 25px; display: flex; align-items: center; gap: 8px;
    font-size: 15.5px; letter-spacing: 0.2px;
  }
  .help svg { width: 38px; height: 32px; }
  .page-code { position: absolute; left: 1160px; top: 28px; font-size: 12px; }
</style>
</head>
<body>
  <div class="city-backdrop" role="img" aria-label="Faded city skyline photograph behind the report tiles"></div>

  <header class="site-header">
    <div class="brand">
      <span class="brand-mark"></span>
      <span class="brand-name">CSU M&amp;I</span>
    </div>
    <nav class="main-nav">
      <a class="is-active" href="#">Finance</a>
      <a href="#">Gm View</a>
      <a href="#">MI</a>
      <a href="#">General Accounting</a>
      <a href="#">Tax</a>
      <a href="#">Treasury</a>
      <a href="#">Knowledge</a>
    </nav>
    <div class="search">
      <div class="search-field">Search</div>
      <div class="search-buttons">
        <span><svg width="14" height="14" viewBox="0 0 14 14"><circle cx="6" cy="6" r="4.2" fill="none" stroke="#9a9a9a" stroke-width="1.8"/><line x1="9" y1="9" x2="12.5" y2="12.5" stroke="#9a9a9a" stroke-width="2"/></svg></span>
        <span>X</span>
      </div>
    </div>
  </header>

  <svg width="0" height="0" style="position:absolute">
    <defs>
      <symbol id="icon-mail" viewBox="0 0 13 13"><rect width="13" height="13" rx="2.5" fill="#4f67a4"/><path d="M3 4.3h7v4.6H3z" fill="#fff"/><path d="M3 4.3l3.5 2.6 3.5-2.6" fill="none" stroke="#4f67a4" stroke-width="1"/></symbol>
      <symbol id="icon-wrench" viewBox="0 0 14 14"><path d="M12.6 3.2l-2 2-1.8-.3-.3-1.8 2-2A3.6 3.6 0 0 0 6 5.6L1.2 10.4a1.4 1.4 0 0 0 2 2L8 7.6a3.6 3.6 0 0 0 4.6-4.4z"/></symbol>
      <symbol id="icon-doc" viewBox="0 0 14 14"><path d="M2.5 0.5h6l3 3v10h-9zM3.7 1.7v10.6h6.6V4.2H8V1.7z"/><rect x="4.7" y="6" width="4.6" height="1"/><rect x="4.7" y="8" width="4.6" height="1"/><rect x="4.7" y="10" width="4.6" height="1"/></symbol>
      <symbol id="icon-chart" viewBox="0 0 14 14"><rect x="0.5" y="1" width="1.2" height="12"/><rect x="0.5" y="12" width="13" height="1.2"/><rect x="3" y="6" width="1.8" height="6"/><rect x="6" y="3" width="1.8" height="9"/><rect x="9" y="5" width="1.8" height="7"/><rect x="11.7" y="7" width="1.6" height="5"/></symbol>
    </defs>
  </svg>

  <main class="report-grid">
    <article class="report-tile"><div class="report-title"><svg><use href="#icon-mail"/></svg>B &amp; AT Revenue &amp; Margin Analysis</div><div class="report-tools"><svg><use href="#icon-wrench"/></svg><svg><use href="#icon-doc"/></svg><svg><use href="#icon-chart"/></svg></div></article>
    <article class="report-tile"><div class="report-title"><svg><use href="#icon-mail"/></svg>Bold</div><div class="report-tools"><svg><use href="#icon-wrench"/></svg><svg><use href="#icon-doc"/></svg><svg><use href="#icon-chart"/></svg></div></article>
    <article class="report-tile"><div class="report-title"><svg><use href="#icon-mail"/></svg>BSQ Dashboard</div><div class="report-tools"><svg><use href="#icon-wrench"/></svg><svg><use href="#icon-doc"/></svg><svg><use href="#icon-chart"/></svg></div></article>
    <article class="report-tile"><div class="report-title"><svg><use href="#icon-mail"/></svg>Global JV Trends</div><div class="report-tools"><svg><use href="#icon-wrench"/></svg><svg><use href="#icon-doc"/></svg><svg><use href="#icon-chart"/></svg></div></article>
    <article class="report-tile"><div class="report-title"><svg><use href="#icon-mail"/></svg>Inventory Reconciliations</div><div class="report-tools"><svg><use href="#icon-wrench"/></svg><svg><use href="#icon-doc"/></svg><svg><use href="#icon-chart"/></svg></div></article>
    <article class="report-tile"><div class="report-title"><svg><use href="#icon-mail"/></svg>Larkin Inventory Indicators</div><div class="report-tools"><svg><use href="#icon-wrench"/></svg><svg><use href="#icon-doc"/></svg><svg><use href="#icon-chart"/></svg></div></article>
    <article class="report-tile"><div class="report-title"><svg><use href="#icon-mail"/></svg>Mi BS Metrics</div><div class="report-tools"><svg><use href="#icon-wrench"/></svg><svg><use href="#icon-doc"/></svg><svg><use href="#icon-chart"/></svg></div></article>
    <article class="report-tile"><div class="report-title"><svg><use href="#icon-mail"/></svg>MI Negative Inventory</div><div class="report-tools"><svg><use href="#icon-wrench"/></svg><svg><use href="#icon-doc"/></svg><svg><use href="#icon-chart"/></svg></div></article>
    <article class="report-tile"><div class="report-title"><svg><use href="#icon-mail"/></svg>Mi PCPR</div><div class="report-tools"><svg><use href="#icon-wrench"/></svg><svg><use href="#icon-doc"/></svg><svg><use href="#icon-chart"/></svg></div></article>
    <article class="report-tile"><div class="report-title"><svg><use href="#icon-mail"/></svg>MI PO Performance</div><div class="report-tools"><svg><use href="#icon-wrench"/></svg><svg><use href="#icon-doc"/></svg><svg><use href="#icon-chart"/></svg></div></article>
    <article class="report-tile"><div class="report-title"><svg><use href="#icon-mail"/></svg>Nam Balance Sheet Online Tool</div><div class="report-tools"><svg><use href="#icon-wrench"/></svg><svg><use href="#icon-doc"/></svg><svg><use href="#icon-chart"/></svg></div></article>
    <article class="report-tile"><div class="report-title"><svg><use href="#icon-mail"/></svg>Reporter - Finance Consolidated</div><div class="report-tools"><svg><use href="#icon-wrench"/></svg><svg><use href="#icon-doc"/></svg><svg><use href="#icon-chart"/></svg></div></article>
    <article class="report-tile"><div class="report-title"><svg><use href="#icon-mail"/></svg>Sort</div><div class="report-tools"><svg><use href="#icon-wrench"/></svg><svg><use href="#icon-doc"/></svg><svg><use href="#icon-chart"/></svg></div></article>
    <article class="report-tile"><div class="report-title"><svg><use href="#icon-mail"/></svg>Sort Utilization</div><div class="report-tools"><svg><use href="#icon-wrench"/></svg><svg><use href="#icon-doc"/></svg><svg><use href="#icon-chart"/></svg></div></article>
  </main>

  <footer class="site-footer">
    <p class="copyright">(c) 2015 CSU M&amp;I. All rights reserved.</p>
    <div class="social">
      <span class="share-tile"></span>
      <span class="share-tile"></span>
      <span class="share-tile"></span>
      <svg viewBox="0 0 19 19"><rect width="19" height="19" rx="4" fill="#fff"/><path d="M6 3.5l2 .3.8 3-1.4 1.2a8 8 0 0 0 3.6 3.6l1.2-1.4 3 .8.3 2-1.6 1.6C9.5 15 4 9.5 4.4 5.1z" fill="#5068a6"/></svg>
    </div>
    <div class="help">HELP &amp; FEEDBACK
      <svg viewBox="0 0 38 32"><path d="M1.5 1.5h35v22H14l-4 6v-6H1.5z" fill="none" stroke="#fff" stroke-width="1.5"/><text x="19" y="17" text-anchor="middle" font-family="Open Sans, sans-serif" font-weight="600" font-size="14" fill="#fff">?</text></svg>
    </div>
    <span class="page-code">C7</span>
  </footer>
</body>
</html>
```